Personal Injury Mailer for a Chiropractic Office

I need a postcard design for our new Chiropractic office called "Birch Chiropractic". I am looking to treat more traumatic injuries such as those caused by auto accidents. I treat using gentle Chiropractic care in combination with Deep Glide Methods soft tissue massage.

I like some of the elements of the uploaded .jpgs: the smashed car on the one and the lady rubbing her neck and back on the other. I DO NOT like the soft collar neck brace. I would rather the person in the picture be female than male. I am only mailing to potential clients who are not at fault, so I want to communicate to them that their treatment will, in all probability, be at no cost to them. I like the message on the "If you've been in an auto accident, the real damage may not be this obvious" or something to that effect. So many people neglect to get proper treatment after an accident and the effects of these injuries show up down the road.

Please include my headshot (not prominently). Please include "Let us review your case. Schedule a Consult today and receive a FREE tube of Muscavel Pain Reliever ($10 value)." [$10 value in small print] The phrases: "This is an advertisement for chiropractic services." and "If you decide to purchase additional treatment, you have the legal right to change your mind within three days and receive a refund." must be included as disclaimers in small print. They can be place on the address side of the postcard.

I have also included my logo in a few different formats and 3 versions of the DGM/Stormfox logo.
(555) 730-4418
www.birchchiro.example

```html
<!DOCTYPE html>
<html lang="en">
<head>
<meta charset="utf-8">
<title>Birch Chiropractic – Personal Injury Mailer</title>
<link rel="stylesheet" href="https://fonts.googleapis.com/css2?family=Lato:wght@300;400;700&family=Bitter:ital,wght@1,400&family=Cinzel:wght@400&display=swap">
<style>
  :root {
    --frame-light: #e08a3a;
    --frame-dark: #b9571a;
    --card: #fbfbfb;
    --card-shade: #eeeeef;
    --ink: #1f1f1f;
    --tagline: #3b3a8e;
    --accent-blue: #1b7fc4;
    --sky: #5cc6e8;
    --badge-red: #d32027;
    --divider: #2a6fb0;
  }
  * { margin: 0; padding: 0; box-sizing: border-box; }
  html, body { width: 1200px; height: 784px; overflow: hidden; background: #ffffff; }
  .postcard {
    position: relative;
    width: 1200px; height: 784px;
    background: linear-gradient(135deg, var(--frame-light), var(--frame-dark) 55%, var(--frame-light));
    padding: 14px;
  }
  .card {
    position: relative;
    width: 100%; height: 100%;
    border-radius: 4px;
    overflow: hidden;
    background: radial-gradient(ellipse at 40% 45%, var(--card) 40%, var(--card-shade) 100%);
  }
  .brand {
    position: absolute; left: 42px; top: 86px;
    display: flex; align-items: center; gap: 12px;
    font-family: "Cinzel", serif; font-size: 31px; color: var(--ink);
    letter-spacing: 1px;
  }
  .brand-dot { width: 18px; height: 18px; border-radius: 50%; background: var(--sky); }
  .tagline {
    position: absolute; left: 422px; top: 84px;
    font-family: "Bitter", serif; font-style: italic; font-size: 21px; line-height: 1.3;
    color: var(--tagline);
  }
  .offer {
    position: absolute; left: 44px; top: 234px; width: 760px;
    font-family: "Lato", sans-serif; font-weight: 400; font-size: 36px; line-height: 60px;
    color: var(--ink);
  }
  .offer small { font-size: 21px; }
  .injury-photo {
    position: absolute; left: 848px; top: 120px;
    width: 520px; height: 520px; border-radius: 50%;
    border: 26px solid var(--sky);
    background: linear-gradient(180deg, #c8232a 0%, #a61c22 40%, #e6a6a6 62%, #e58cb8 80%, #d96aa6 100%);
  }
  .partners {
    position: absolute; left: 44px; top: 544px;
    display: flex; align-items: center; gap: 26px;
    font-family: "Lato", sans-serif;
  }
  .partner-dgm { display: flex; align-items: center; gap: 10px; font-weight: 700; font-size: 30px; color: var(--badge-red); }
  .partner-dgm .badge { width: 26px; height: 26px; border-radius: 50%; background: var(--badge-red); }
  .partner-dgm span.full { font-size: 16px; }
  .partner-divider { width: 2px; height: 70px; background: var(--divider); }
  .partner-stormfox { color: var(--accent-blue); font-weight: 700; }
  .partner-stormfox .kicker { font-size: 13px; letter-spacing: 0.5px; display: block; }
  .partner-stormfox .name { font-size: 30px; letter-spacing: 1px; }
  .contact {
    position: absolute; left: 44px; top: 642px;
    display: flex; gap: 70px;
    font-family: "Lato", sans-serif; font-size: 25px; color: var(--ink);
  }
  .contact-item { display: flex; align-items: center; gap: 8px; }
  .disclaimer {
    position: absolute; left: 44px; top: 692px; width: 1110px;
    font-family: "Lato", sans-serif; font-size: 17px; line-height: 1.45; color: var(--ink);
  }
</style>
</head>
<body>
<main class="postcard">
  <section class="card">
    <div class="brand"><span class="brand-dot"></span>Birch Chiropractic</div>
    <p class="tagline">"If you've been in an auto accident,<br>the real damage may not be this obvious"</p>

    <p class="offer">"Let us Review your case.<br>Schedule a Consult Today and<br>Receive a FREE tube of Muscavel Pain<br>Reliever <small>($10 value)</small>"</p>

    <div class="injury-photo" role="img" aria-label="Photo of a smashed red car with a woman in a pink top holding her neck and back in pain"></div>

    <div class="partners">
      <div class="partner-dgm"><span class="badge"></span>DGM <span class="full">Deep Glide Methods</span></div>
      <div class="partner-divider"></div>
      <div class="partner-stormfox"><span class="kicker">PROUD PARTNER</span><span class="name">STORMFOX</span></div>
    </div>

    <div class="contact">
      <span class="contact-item">
        <svg width="24" height="24" viewBox="0 0 24 24" aria-hidden="true"><circle cx="12" cy="12" r="11" fill="none" stroke="#1f1f1f" stroke-width="1.6"/><path d="M8 6c-1 1-1.5 2.5 0 5s4 5 6 5.5c1.2.3 2-.2 2.6-1l-2-2-1.3.8c-1.3-.6-2.8-2.1-3.4-3.4l.8-1.3z" fill="#1f1f1f"/></svg>
        (555) 730-4418
      </span>
      <span class="contact-item">
        <svg width="20" height="20" viewBox="0 0 20 20" aria-hidden="true"><g fill="none" stroke="#1f1f1f" stroke-width="1.5"><circle cx="10" cy="10" r="8.5"/><ellipse cx="10" cy="10" rx="3.8" ry="8.5"/><path d="M1.5 10h17M3 5.5h14M3 14.5h14"/></g></svg>
        www.birchchiro.example
      </span>
    </div>

    <p class="disclaimer">Disclaimers: "This is an advertisement for chiropractic services." and "If you decide to purchase additional treatment, you have the legal right to change your mind within three days and receive a refund."</p>
  </section>
</main>
</body>
</html>
```